holloway paving service

Needs to have phone number 0418259730 and email markholloway@brightmail.com.au.
ABN 62318470915
name mark holloway

For all your concreting solutions
Excavation
Exposed & colour concrete
House & shed slabs
Driveways
Landing & steps

Contact Information for Business Card

ph 0418259730
email markholloway@brightmail.com.au.
ABN 62318470915
name mark holloway

```html
<!DOCTYPE html>
<html lang="en">
<head>
<meta charset="utf-8">
<title>Holloway Paving Service – Business Card</title>
<link rel="stylesheet" href="https://fonts.googleapis.com/css2?family=Montserrat:wght@600;700&family=Roboto:wght@400&display=swap">
<style>
  :root {
    --backdrop: #2c2c2c;
    --card-white: #f3f3f3;
    --brand-orange: #f26b22;
    --brand-grey: #6b6b6b;
    --text-white: #ffffff;
  }
  * { box-sizing: border-box; margin: 0; padding: 0; }
  html, body {
    width: 1200px;
    height: 960px;
    overflow: hidden;
    background: var(--backdrop);
  }
  .canvas {
    position: relative;
    width: 1200px;
    height: 960px;
  }
  .card {
    position: absolute;
    width: 600px;
    height: 342px;
    overflow: hidden;
    box-shadow: 0 3px 6px rgba(0,0,0,0.45);
  }

  /* Front */
  .card-front {
    left: 322px;
    top: 110px;
    background: var(--card-white);
  }
  .brand-block {
    position: absolute;
    left: 0;
    top: 73px;
    width: 100%;
    height: 80px;
  }
  .brand-square {
    position: absolute;
    left: 170px;
    top: 21px;
    width: 38px;
    height: 38px;
    background: var(--brand-grey);
  }
  .brand-divider {
    position: absolute;
    left: 243px;
    top: 0;
    width: 2px;
    height: 80px;
    background: var(--brand-orange);
  }
  .brand-text {
    position: absolute;
    left: 251px;
    top: 19px;
    text-align: center;
    font-family: "Montserrat", sans-serif;
    color: var(--brand-orange);
    white-space: nowrap;
  }
  .brand-name {
    font-weight: 700;
    font-size: 14px;
    line-height: 18px;
    letter-spacing: 0.2px;
  }
  .brand-phone {
    margin-top: 12px;
    font-weight: 600;
    font-size: 13px;
    line-height: 16px;
    letter-spacing: 1px;
  }
  .base-band {
    position: absolute;
    bottom: 0;
    height: 14px;
    background: var(--brand-grey);
  }
  .base-band-left { left: 0; width: 131px; }
  .base-band-right { right: 0; width: 131px; }
  .contact-panel {
    position: absolute;
    left: 135px;
    top: 241px;
    width: 331px;
    height: 101px;
    background: var(--brand-orange);
    border: 4px solid var(--brand-grey);
    border-bottom: none;
    text-align: center;
    color: var(--text-white);
    font-family: "Montserrat", sans-serif;
    font-weight: 700;
  }
  .contact-name {
    margin-top: 18px;
    font-size: 21px;
    letter-spacing: 0.5px;
    line-height: 26px;
  }
  .contact-line {
    font-size: 13px;
    line-height: 20px;
    letter-spacing: 0.3px;
  }

  /* Back */
  .card-back {
    left: 320px;
    top: 493px;
    background: var(--brand-orange);
    text-align: center;
    color: var(--text-white);
  }
  .back-name {
    position: absolute;
    left: 0;
    top: 128px;
    width: 100%;
    font-family: "Montserrat", sans-serif;
    font-weight: 700;
    font-size: 28px;
    line-height: 34px;
    letter-spacing: 1px;
  }
  .services {
    position: absolute;
    left: 0;
    top: 270px;
    width: 100%;
    font-family: "Roboto", sans-serif;
    font-size: 14.5px;
    line-height: 18px;
  }
  .services .sep {
    font-size: 9px;
    vertical-align: 2px;
    margin: 0 3px;
  }
</style>
</head>
<body>
<div class="canvas">

  <section class="card card-front" aria-label="Business card front">
    <div class="brand-block">
      <div class="brand-square"></div>
      <div class="brand-divider"></div>
      <div class="brand-text">
        <p class="brand-name">HOLLOWAY PAVING SERVICE</p>
        <p class="brand-phone">0418259730</p>
      </div>
    </div>
    <div class="base-band base-band-left"></div>
    <div class="base-band base-band-right"></div>
    <div class="contact-panel">
      <p class="contact-name">MARK HOLLOWAY</p>
      <p class="contact-line">MARKHOLLOWAY@BRIGHTMAIL.COM.AU</p>
      <p class="contact-line">ABN 62318470915</p>
    </div>
  </section>

  <section class="card card-back" aria-label="Business card back">
    <p class="back-name">HOLLOWAY PAVING<br>SERVICE</p>
    <div class="services">
      <p>Excavation<span class="sep">◆</span>Exposed &amp; colour concrete</p>
      <p>House &amp; shed slabs<span class="sep">◆</span>Driveways<span class="sep">◆</span>Landing &amp; steps</p>
    </div>
  </section>

</div>
</body>
</html>
```